The logo name is "Harbor Skin". The name of the product will be "Cutaneous Comfort". This product is specifically formulated for amputees. Therefore under the product name it should state "for amputees". The catch phrase will be "Experience Harbor find Calmness"
These are the things we need on the label:
Logo, product name, "for amputees", "Experience Harbor find Calmness", Safe, Effective, Directions: spray on problem areas, no need to dry off. harborskin.example, Made in Canada, 500ml.
The MOST IMPORTANT and therefore the most prominent thing on this lable will be the LOGO! The second most prominent thing will be the word "Comfort" We want to keep it very plain, very simple, very unclutered. Keep in mind that this lable will be placed on a white bottle or have a white back ground. The 500ml white PE bottle with trigger sprayer will have a tear drop label. See attached die line (S-294).
We want to stay with the colours that goes with the colour scheme of the logo. See attached logo. Soft colours. We do not want a picture! We would like the lable to be classy and rich.
Updates
The logo name is "Harbor Skin". The name of the product will be "Cutaneous Comfort". This product is specificlly formulated for amputees. Therefore under the product name it should state "for amputees". The catch phrase will be "Experience Harbor find Calmness"
Logo, product name, "for amputees", catch phrase "Experience Harbor find Calmness", Clean, Safe, Effective, Directions: spray on problem areas, no need to dry off. Also Harbor Skin Corpation, harborskin.example, Made in Canada, 500ml.
We want to stay with the colour scheme of the logo. See attached logo. Soft colours. We do not want a picture! We would like the lable to be classy and rich.
This is the offical directive that came from the governing panal of this lable. This panal it not know where it wanted to take this lable that would represent this line until they review all of your submissions, thank you for all your talented hard work. But now it is clear it is time to regroup and hit this objective.
Project Deadline Extended
Reason: New restrictions on lable wording for this product.
Target Market(s)
Amputees and Parents of.
Industry/Entity Type
Product
Requirements
Must have
- Final product to be in a pdf or an illustrator file

```html
<!DOCTYPE html>
<html lang="en">
<head>
<meta charset="utf-8">
<title>Harbor Skin – Cutaneous Comfort label</title>
<link rel="stylesheet" href="https://fonts.googleapis.com/css2?family=Gelasio:wght@400;500&family=Arimo&display=swap">
<style>
  :root {
    --ink-green: #146d55;
    --teal: #2cb3b0;
    --teal-soft: #cfeceb;
    --teal-pale: #eaf7f6;
    --label-edge: #e3e8e8;
    --caption: #444;
    --paper: #ffffff;
  }
  * { margin: 0; padding: 0; box-sizing: border-box; }
  html, body { width: 1200px; height: 919px; overflow: hidden; background: var(--paper); }
  .canvas { position: relative; width: 1200px; height: 919px; font-family: "Gelasio", Georgia, serif; color: var(--ink-green); }

  .brand-mark { position: absolute; display: flex; align-items: center; gap: 8px; }
  .brand-mark .mark-square { background: var(--teal); opacity: .75; }
  .brand-mark .mark-name { color: var(--ink-green); font-weight: 500; white-space: nowrap; }

  .corner-brand { left: 28px; top: 34px; }
  .corner-brand .mark-square { width: 34px; height: 34px; }
  .corner-brand .mark-name { font-size: 27px; }

  .label { position: absolute; top: 355px; width: 260px; height: 452px; }
  .label-front { left: 182px; }
  .label-back { left: 773px; }
  .label-shape { position: absolute; inset: 0; }

  .label-text { position: absolute; left: 0; right: 0; text-align: center; }
  .tagline { top: 112px; font-size: 13px; line-height: 17px; color: var(--teal); }
  .product-name { font-size: 18px; color: var(--ink-green); }
  .audience { font-size: 15px; color: var(--teal); }
  .claims { font-size: 15px; font-weight: 500; }
  .directions { font-size: 10.5px; line-height: 15px; }
  .web { font-family: "Arimo", Arial, sans-serif; font-size: 7.5px; }
  .volume { font-family: "Arimo", Arial, sans-serif; font-size: 14px; color: #1f3f38; }
  .origin { font-family: "Arimo", Arial, sans-serif; font-size: 7.5px; color: #1f3f38; }

  .label-front .brand-mark { top: 228px; left: 0; right: 0; justify-content: center; }
  .label-front .mark-square { width: 40px; height: 40px; }
  .label-front .mark-name { font-size: 27px; }

  .label-back .brand-mark { top: 128px; left: 146px; transform: translateX(-50%); }
  .label-back .mark-square { width: 26px; height: 26px; }
  .label-back .mark-name { font-size: 18px; }

  .view-caption { position: absolute; top: 884px; font-family: "Arimo", Arial, sans-serif; font-size: 8px; color: var(--caption); }
</style>
</head>
<body>
<div class="canvas">

  <div class="brand-mark corner-brand">
    <span class="mark-square"></span>
    <span class="mark-name">Harbor Skin</span>
  </div>

  <!-- Front panel -->
  <section class="label label-front" aria-label="Front label">
    <svg class="label-shape" viewBox="0 0 260 452" width="260" height="452">
      <defs>
        <clipPath id="front-die">
          <path d="M130,6 C172,6 186,70 204,140 C222,210 254,270 254,330 L254,424 Q254,446 232,446 L28,446 Q6,446 6,424 L6,330 C6,270 38,210 56,140 C74,70 88,6 130,6 Z"/>
        </clipPath>
        <linearGradient id="front-wash" x1="0" y1="0" x2="0" y2="1">
          <stop offset="0" stop-color="#ffffff"/>
          <stop offset="1" stop-color="#c8e9e7"/>
        </linearGradient>
      </defs>
      <path d="M130,6 C172,6 186,70 204,140 C222,210 254,270 254,330 L254,424 Q254,446 232,446 L28,446 Q6,446 6,424 L6,330 C6,270 38,210 56,140 C74,70 88,6 130,6 Z" fill="#fff" stroke="var(--label-edge)" stroke-width="1.5"/>
      <g clip-path="url(#front-die)">
        <rect role="img" aria-label="Soft teal wave texture" x="0" y="285" width="260" height="170" fill="url(#front-wash)"/>
        <path d="M30,152 C90,140 150,146 220,178 C160,158 100,152 30,152 Z" fill="var(--teal)" opacity=".55"/>
        <path d="M40,290 C110,262 170,262 240,268 C170,272 110,278 40,290 Z" fill="var(--teal)" opacity=".55"/>
      </g>
    </svg>
    <p class="label-text tagline">Experience Harbor<br>find Calmness</p>
    <div class="brand-mark">
      <span class="mark-square"></span>
      <span class="mark-name">Harbor Skin</span>
    </div>
    <p class="label-text product-name" style="top:344px">Cutaneous Comfort</p>
    <p class="label-text audience" style="top:369px">for amputees</p>
    <p class="label-text volume" style="top:410px">500ml</p>
    <p class="label-text origin" style="top:426px">Made in Canada</p>
  </section>

  <!-- Back panel -->
  <section class="label label-back" aria-label="Back label">
    <svg class="label-shape" viewBox="0 0 260 452" width="260" height="452">
      <defs>
        <clipPath id="back-die">
          <path d="M130,6 C172,6 186,70 204,140 C222,210 254,270 254,330 L254,424 Q254,446 232,446 L28,446 Q6,446 6,424 L6,330 C6,270 38,210 56,140 C74,70 88,6 130,6 Z"/>
        </clipPath>
        <linearGradient id="back-wash" x1="0" y1="0" x2="0" y2="1">
          <stop offset="0" stop-color="#ffffff"/>
          <stop offset="1" stop-color="#c8e9e7"/>
        </linearGradient>
      </defs>
      <path d="M130,6 C172,6 186,70 204,140 C222,210 254,270 254,330 L254,424 Q254,446 232,446 L28,446 Q6,446 6,424 L6,330 C6,270 38,210 56,140 C74,70 88,6 130,6 Z" fill="#fff" stroke="var(--label-edge)" stroke-width="1.5"/>
      <g clip-path="url(#back-die)">
        <rect role="img" aria-label="Soft teal wave texture" x="0" y="300" width="260" height="155" fill="url(#back-wash)"/>
        <path d="M40,172 C110,156 170,152 230,152 C170,160 110,166 40,172 Z" fill="var(--teal)" opacity=".55"/>
        <path d="M20,310 C90,290 170,270 230,262 C170,276 100,294 20,310 Z" fill="var(--teal)" opacity=".55"/>
      </g>
    </svg>
    <div class="brand-mark">
      <span class="mark-square"></span>
      <span class="mark-name">Harbor Skin</span>
    </div>
    <p class="label-text product-name" style="top:218px">Cutaneous Comfort</p>
    <p class="label-text audience" style="top:241px">for amputees</p>
    <p class="label-text claims" style="top:327px">Safe Effective</p>
    <p class="label-text directions" style="top:349px">Directions: spray on problem areas,<br>no need to dry off</p>
    <p class="label-text web" style="top:392px">www.harborskin.example</p>
    <p class="label-text volume" style="top:413px">500ml</p>
    <p class="label-text origin" style="top:429px">Made in Canada</p>
  </section>

  <p class="view-caption" style="left:291px">front</p>
  <p class="view-caption" style="left:897px">back</p>
</div>
</body>
</html>
```